A Kettle for Distant Orchards

I want the title to look like it’s painted with a paintbrush. This is also a story about my relationship with a spirit of a famous Venetian painter from the 1800s so paint references and swirls are encouraged. The story takes place in Chicago; Bali; Venice, Italy; Sedona, Arizona; and Paris, France. Venice is the most important place. I attached a photo that may make a good cover photo

Target Market(s)

For those interested in travel, spirituality, healing

Requirements
Must have
• The title should look like it’s painted and be flowy
Nice to have
• Story takes place in Venice Italy. Any Venice symbolism would be great

```html
<!DOCTYPE html>
<html lang="en">
<head>
<meta charset="utf-8">
<title>A Kettle for Distant Orchards — Cover Wrap</title>
<link href="https://fonts.googleapis.com/css2?family=Caveat+Brush&family=Montserrat:wght@400&family=Jost:wght@400&display=swap" rel="stylesheet">
<style>
  :root {
    --backdrop: #262626;
    --paper: #ffffff;
    --title-ink: #1d3b3b;
    --body-ink: #222222;
    --author-ink: #333333;
    --stone: #cbbfae;
    --brick: #a88f7d;
    --canal: #5f8f84;
    --canal-deep: #2f4f4a;
  }
  * { margin: 0; padding: 0; box-sizing: border-box; }
  html, body { width: 1200px; height: 1200px; overflow: hidden; }
  body { background: var(--backdrop); position: relative; }

  .cover-wrap {
    position: absolute; left: 30px; top: 207px;
    width: 1140px; height: 786px;
    background: var(--paper);
  }

  .title {
    font-family: "Caveat Brush", cursive;
    color: var(--title-ink);
    text-transform: uppercase;
    text-align: center;
    font-weight: 400;
    position: absolute;
  }

  .back-cover { position: absolute; left: 0; top: 0; width: 515px; height: 100%; }
  .back-cover .title { left: 0; width: 515px; top: 70px; font-size: 48px; line-height: 46px; }
  .blurb {
    position: absolute; left: 32px; width: 452px;
    font-family: "Montserrat", sans-serif;
    font-size: 13.4px; line-height: 19.5px;
    color: var(--body-ink);
    text-align: justify; text-align-last: center;
  }
  .blurb-first { top: 232px; }
  .blurb-second { top: 407px; }

  .spine {
    position: absolute; left: 545px; top: 0; width: 48px; height: 100%;
  }
  .spine-title {
    position: absolute; left: 4px; top: 38px;
    writing-mode: vertical-rl;
    font-family: "Caveat Brush", cursive;
    text-transform: uppercase;
    font-size: 40px; line-height: 40px;
    color: var(--title-ink);
    white-space: nowrap;
  }
  .spine-author {
    position: absolute; left: 10px; top: 552px;
    writing-mode: vertical-rl;
    font-family: "Jost", sans-serif;
    font-size: 27px; letter-spacing: 1px;
    color: var(--author-ink);
    white-space: nowrap;
  }

  .front-cover { position: absolute; left: 615px; top: 0; width: 525px; height: 100%; }
  .front-cover .title { left: 0; width: 525px; top: 42px; font-size: 92px; line-height: 88px; }
  .cover-scene { position: absolute; left: 10px; top: 318px; width: 510px; height: 378px; }
  .author-name {
    position: absolute; left: 0; width: 525px; top: 708px;
    text-align: center;
    font-family: "Jost", sans-serif;
    font-size: 37px; letter-spacing: 0.5px;
    color: var(--author-ink);
  }
</style>
</head>
<body>
  <main class="cover-wrap">
    <section class="back-cover">
      <h2 class="title">A Kettle<br>For Distant<br>Orchards</h2>
      <p class="blurb blurb-first">Lorem ipsum dolor sit amet, consectetur adipiscing elit, sed do eiusmod tempor incididunt ut labore et dolore magna aliqua. Quis ipsum suspendisse ultrices gravida. Risus commodo viverra maecenas accumsan lacus vel facilisis. Lorem ipsum dolor sit amet, consectetur adipiscing elit, sed do eiusmod tempor incididunt ut labore et dolore magna aliqua. Quis ipsum suspendisse ultrices gravida. Risus commodo viverra maecenas accumsan lacus vel facilisis.</p>
      <p class="blurb blurb-second">Lorem ipsum dolor sit amet, consectetur adipiscing elit, sed do eiusmod tempor incididunt ut labore et dolore magna aliqua. Quis ipsum suspendisse ultrices gravida. Risus commodo viverra maecenas accumsan lacus vel facilisis. Lorem ipsum dolor sit amet, consectetur adipiscing elit, sed do eiusmod tempor incididunt ut labore et dolore magna aliqua. Quis ipsum suspendisse ultrices gravida. Risus commodo viverra maecenas accumsan lacus vel facilisis. Lorem ipsum dolor sit amet, consectetur adipiscing elit, sed do eiusmod tempor incididunt ut labore et dolore magna aliqua. Quis ipsum suspendisse ultrices gravida. Risus commodo viverra maecenas accumsan lacus vel facilisis.</p>
    </section>

    <section class="spine">
      <span class="spine-title">A Kettle for Distant Orchards</span>
      <span class="spine-author">AUTHOR NAME</span>
    </section>

    <section class="front-cover">
      <h1 class="title">A Kettle<br>For Distant<br>Orchards</h1>
      <svg class="cover-scene" viewBox="0 0 510 378" role="img" aria-label="Painterly brush-stroke image of a Venetian canal with an arched stone bridge between old buildings">
        <defs>
          <linearGradient id="canalTones" x1="0" y1="0" x2="0" y2="1">
            <stop offset="0" stop-color="var(--stone)"/>
            <stop offset="0.4" stop-color="var(--brick)"/>
            <stop offset="0.62" stop-color="var(--canal-deep)"/>
            <stop offset="1" stop-color="var(--canal)"/>
          </linearGradient>
        </defs>
        <path fill="url(#canalTones)" d="M70 120 L120 40 L150 30 L190 20 L230 30 L260 12 L300 40 L340 10 L380 0 L410 30 L440 60 L470 110 L500 160 L490 190 L505 215 L470 230 L470 260 L430 275 L440 300 L380 310 L410 335 L330 345 L350 365 L220 370 L120 360 L110 335 L80 320 L40 310 L55 280 L10 265 L30 240 L5 200 L30 170 Z"/>
      </svg>
      <p class="author-name">AUTHOR NAME</p>
    </section>
  </main>
</body>
</html>
```